PlumVesta screens tidy up

We would like advice on how to better present the following home page and overview pages.

The existing website is functional, but the pages don't appear professionals and pleasing to the eye. We would specifically like feedback on alignment and padding of icons and text to make the screen more appealing and polished.

We are following the quartzline design system.

1 page

Sans Serif
• IBM Plex, Poppins

```html
<!DOCTYPE html>
<html lang="en">
<head>
<meta charset="utf-8">
<title>PlumVesta – Home and Overview screens</title>
<link href="https://fonts.googleapis.com/css2?family=Poppins:wght@400;500;600;700&display=swap" rel="stylesheet">
<style>
:root{
  --stage:#979797;
  --navy:#0f2149;
  --side:#243150;
  --side-dark:#15264c;
  --side-line:#2f3c5b;
  --orange:#f0a33a;
  --content:#ebebeb;
  --panel:#ffffff;
  --beige:#fcf4e8;
  --grey-card:#f2f2f2;
  --ink:#1b1b1b;
  --muted:#333a44;
  --rule:#e4e4e4;
}
*{box-sizing:border-box;margin:0;padding:0}
html,body{width:724px;height:1200px;overflow:hidden;background:var(--stage)}
body{font-family:"Poppins",sans-serif;color:var(--ink)}
.stage{position:absolute;left:0;top:0;width:1486px;height:2464px;transform:scale(.48721);transform-origin:0 0}
.screen{position:absolute;left:30px;width:1425px;height:1168px;background:var(--content);overflow:hidden}
.screen--home{top:33px}
.screen--overview{top:1231px}
.abs{position:absolute}

/* header */
.topbar{position:absolute;left:0;top:0;width:1425px;height:92px;background:var(--navy)}
.brand{position:absolute;left:37px;top:26px;display:flex;align-items:center;gap:10px;color:#fff;font-size:20px;font-weight:500}
.brand-dot{width:30px;height:30px;border-radius:50%;background:var(--orange)}
.avatar{position:absolute;left:1235px;top:20px;width:54px;height:54px;border-radius:50%;background:radial-gradient(circle at 50% 40%,#b98d74,#5b6a80)}
.welcome{position:absolute;left:1300px;top:28px;color:#fff;font-size:13px;line-height:1.2}
.welcome b{display:block;font-size:17px;font-weight:500;margin-top:5px}
.caret{position:absolute;left:1368px;top:38px}

/* sidebar */
.sidebar{position:absolute;left:0;top:92px;width:220px;height:1076px;background:var(--side)}
.search{position:absolute;left:19px;top:32px;width:171px;height:27px;border:2px solid #fff;border-radius:14px;color:#fff;font-size:11px;padding:4px 0 0 17px}
.search-btn{position:absolute;right:2px;top:2px;width:19px;height:19px;border-radius:50%;background:#fff}
.nav{position:absolute;left:0;top:72px;width:220px;list-style:none}
.nav li{position:relative;height:42px;border-bottom:1px solid var(--side-line);color:#fff;font-size:12px;font-weight:600;display:flex;align-items:center;padding-left:49px}
.nav li.sub{padding-left:54px}
.nav li.active{background:var(--orange);border-bottom-color:var(--orange)}
.nav li.group{background:var(--side-dark);border-bottom-color:var(--side-dark)}
.nav .ico{position:absolute;left:25px;top:14px;width:14px;height:14px}
.nav li.sub .ico{left:24px}
.nav .end{position:absolute;right:12px;top:15px}

/* content */
.panel{position:absolute;left:232px;width:1168px;background:var(--panel)}
.panel-head{height:49px;border-bottom:3px solid var(--rule);font-size:12px;color:var(--muted);padding:17px 0 0 13px;position:relative}
.panel-head .right-label{position:absolute;left:605px;top:17px}
.eyebrow{position:absolute;left:13px;color:var(--orange);font-size:19px;font-weight:600}
.btn-new{position:absolute;background:var(--navy);color:var(--orange);font-size:12px;font-weight:500;display:flex;align-items:center;justify-content:center;gap:8px}
.card{position:absolute;width:555px}
.card--beige{background:var(--beige)}
.card--grey{background:var(--grey-card)}
.icon-disc{position:absolute;width:70px;height:70px;border-radius:50%;background:var(--side);display:flex;align-items:center;justify-content:center}
.badge{position:absolute;width:43px;height:43px;border-radius:50%;display:flex;align-items:center;justify-content:center}
.badge--orange{background:var(--orange)}
.badge--navy{background:var(--side)}
.card-title{position:absolute;font-size:20px;font-weight:600;color:var(--ink)}
.small{position:absolute;font-size:12px;color:var(--muted)}
.big-num{position:absolute;font-size:30px;font-weight:700;color:var(--navy)}
.camp-card{position:absolute;top:106px;width:287px;height:291px;border-radius:4px}
.camp-card--grey{background:var(--grey-card)}
.camp-card--white{background:#fff;border:1px solid #e6e6e6}
.camp-title{position:absolute;left:26px;top:104px;font-size:20px;font-weight:600;white-space:nowrap}
.camp-desc{position:absolute;left:27px;top:137px;font-size:11px;color:var(--muted);white-space:nowrap;width:250px;overflow:hidden}
.camp-active{position:absolute;left:33px;top:158px;font-size:20px;font-weight:600;color:var(--navy)}
.camp-active span{color:var(--orange);font-size:25px}
.progress{position:absolute;left:38px;top:147px;width:492px;height:3px;background:#e3e3e8;border-radius:2px}
.progress i{position:absolute;left:0;top:0;width:10px;height:3px;background:var(--navy);border-radius:2px}
</style>
</head>
<body>
<div class="stage">

<!-- ================= HOME ================= -->
<section class="screen screen--home">
  <header class="topbar">
    <div class="brand"><span class="brand-dot"></span>PlumVesta</div>
    <div class="avatar" role="img" aria-label="User profile photo"></div>
    <div class="welcome">Welcome<b>kk.</b></div>
    <svg class="caret" width="12" height="8" viewBox="0 0 12 8"><path d="M1 1l5 5 5-5" fill="none" stroke="#fff" stroke-width="2"/></svg>
  </header>

  <aside class="sidebar">
    <div class="search">Search<span class="search-btn"></span></div>
    <ul class="nav">
      <li class="active"><svg class="ico" viewBox="0 0 14 14"><path d="M1 7l6-5 6 5v6H9V9H5v4H1z" fill="#fff"/></svg><span style="padding-left:7px">Home</span></li>
      <li><svg class="ico" viewBox="0 0 14 14"><path d="M7 1a4 4 0 014 4v4l2 2H1l2-2V5a4 4 0 014-4zM5 12h4a2 2 0 01-4 0z" fill="#fff"/></svg>All Alerts</li>
      <li><svg class="ico" viewBox="0 0 14 14"><circle cx="7" cy="7" r="5" fill="none" stroke="#fff" stroke-width="3" stroke-dasharray="2.2 1.4"/><circle cx="7" cy="7" r="2.5" fill="#fff"/></svg>Mange</li>
      <li><svg class="ico" viewBox="0 0 14 14"><rect x="1" y="2" width="12" height="10" fill="none" stroke="#fff"/><path d="M1 5h12" stroke="#fff"/></svg>Campaigns<svg class="end" width="10" height="10" viewBox="0 0 10 10"><path d="M5 0v10M0 5h10" stroke="#fff" stroke-width="2"/></svg></li>
      <li class="group"><svg class="ico" viewBox="0 0 14 14"><rect x="1" y="2" width="12" height="10" fill="none" stroke="#fff"/><path d="M1 5h12" stroke="#fff"/></svg><span style="padding-left:3px">My Custom Campaign</span><svg class="end" width="11" height="7" viewBox="0 0 11 7"><path d="M1 6l4.5-4.5L10 6" fill="none" stroke="#fff" stroke-width="2"/></svg></li>
      <li class="sub"><svg class="ico" viewBox="0 0 14 14"><rect x="1" y="1" width="12" height="12" fill="none" stroke="#fff"/><circle cx="8" cy="8" r="3" fill="none" stroke="#fff"/></svg>Overview</li>
      <li class="sub"><svg class="ico" viewBox="0 0 14 14"><path d="M3 1h6l3 3v9H3z" fill="none" stroke="#fff"/></svg>Files &amp; HonyTokens</li>
      <li class="sub"><svg class="ico" viewBox="0 0 14 14"><circle cx="7" cy="3" r="2" fill="#fff"/><circle cx="3" cy="9" r="2" fill="#fff"/><circle cx="11" cy="9" r="2" fill="#fff"/><path d="M1 14h12" stroke="#fff"/></svg>Resource</li>
      <li class="sub"><svg class="ico" viewBox="0 0 14 14"><path d="M7 1a4 4 0 014 4v4l2 2H1l2-2V5a4 4 0 014-4zM5 12h4a2 2 0 01-4 0z" fill="#fff"/></svg>Alerts</li>
      <li class="sub"><svg class="ico" viewBox="0 0 14 14"><circle cx="7" cy="7" r="5" fill="none" stroke="#fff" stroke-width="3" stroke-dasharray="2.2 1.4"/><circle cx="7" cy="7" r="2.5" fill="#fff"/></svg>Settings</li>
      <li class="sub group"><svg class="ico" viewBox="0 0 14 14"><rect x="1" y="2" width="12" height="10" fill="none" stroke="#fff"/><path d="M1 5h12" stroke="#fff"/></svg>Default Campaign<svg class="end" width="11" height="7" viewBox="0 0 11 7"><path d="M1 1l4.5 4.5L10 1" fill="none" stroke="#fff" stroke-width="2"/></svg></li>
    </ul>
  </aside>

  <div class="panel" style="top:107px;height:49px"><div class="panel-head" style="border:none">Teamspace</div></div>
  <div class="panel" style="top:160px;height:110px">
    <div class="eyebrow" style="top:22px">DEFAULT</div>
    <div class="small" style="left:13px;top:53px;font-size:13px;color:var(--ink)">The Default Client Is Created As A Part Of Your User Account</div>
  </div>

  <div class="panel" style="top:285px;height:358px">
    <div class="panel-head">Subscription Overview<span class="right-label">Files &amp; HoneyTokens</span></div>
    <div class="card card--beige" style="left:15px;top:69px;height:225px">
      <div class="icon-disc" style="left:29px;top:26px"><svg width="40" height="38" viewBox="0 0 40 38"><path d="M4 14l9-8 8 6 12-9" fill="none" stroke="#fff" stroke-width="2"/><rect x="4" y="22" width="5" height="14" fill="none" stroke="#fff" stroke-width="2"/><rect x="13" y="18" width="5" height="18" fill="none" stroke="#fff" stroke-width="2"/><rect x="22" y="24" width="5" height="12" fill="none" stroke="#fff" stroke-width="2"/><rect x="31" y="15" width="5" height="21" fill="none" stroke="#fff" stroke-width="2"/></svg></div>
      <div class="card-title" style="left:45px;top:102px">Starter Pack Usagr</div>
      <div class="progress"><i></i></div>
      <div class="small" style="left:38px;top:164px">0 Files Active Out Of 10 Allowed</div>
    </div>
    <div class="card card--grey" style="left:597px;top:69px;height:225px">
      <div class="icon-disc" style="left:29px;top:26px"><svg width="44" height="44" viewBox="0 0 44 44"><circle cx="22" cy="22" r="19" fill="none" stroke="#fff" stroke-width="3"/><path d="M22 22L9 36M22 22h19M22 3v19" stroke="#fff" stroke-width="3"/><path d="M27 18v-7M32 18V8M37 18v-4" stroke="#fff" stroke-width="2.5"/></svg></div>
      <div class="card-title" style="left:29px;top:102px">Statistics</div>
    </div>
  </div>

  <div class="panel" style="top:657px;height:471px">
    <div class="panel-head">Campaign</div>
    <div class="btn-new" style="left:1038px;top:4px;width:127px;height:41px">New Campaign <svg width="10" height="10" viewBox="0 0 10 10"><path d="M5 0v10M0 5h10" stroke="#f0a33a" stroke-width="2.4"/></svg></div>

    <div class="camp-card camp-card--grey" style="left:199px">
      <div class="icon-disc" style="left:29px;top:27px"><svg width="42" height="34" viewBox="0 0 42 34"><path d="M6 12h8l14-8v24l-14-8H6z" fill="none" stroke="#fff" stroke-width="2"/><path d="M10 20l3 10h4l-2-10M33 10l4-3M34 16h5M33 22l4 3" stroke="#fff" stroke-width="2"/></svg></div>
      <div class="camp-title">My Custom Campaign</div>
      <div class="camp-desc">This Is My Custom Campaign For Finding!</div>
      <div class="camp-active"><span>0</span>Active</div>
      <div class="small" style="left:27px;top:196px">Files And Honey Tokens</div>
      <div class="small" style="left:27px;top:242px">Active Since : Jul 25 2023 13 : 12</div>
    </div>
    <div class="camp-card camp-card--white" style="left:504px">
      <div class="icon-disc" style="left:28px;top:26px"><svg width="42" height="40" viewBox="0 0 42 40"><rect x="10" y="2" width="12" height="9" fill="none" stroke="#fff" stroke-width="1.6"/><rect x="27" y="8" width="12" height="9" fill="none" stroke="#fff" stroke-width="1.6"/><path d="M27 8l6 5 6-5" fill="none" stroke="#fff" stroke-width="1.6"/><path d="M4 28l12-10 4 12z" fill="none" stroke="#fff" stroke-width="2"/><rect x="28" y="26" width="9" height="10" fill="none" stroke="#fff" stroke-width="2"/></svg></div>
      <div class="camp-title">Default Campagin</div>
      <div class="camp-desc">Define Your Own Mission, Or Combine Differen</div>
      <div class="camp-active"><span>0</span>Active</div>
      <div class="small" style="left:27px;top:196px">Files And Honey Tokens</div>
      <div class="small" style="left:27px;top:242px">Active Since : Jul 25 2023 13 : 12</div>
    </div>
  </div>
</section>

<!-- ================= OVERVIEW ================= -->
<section class="screen screen--overview">
  <header class="topbar">
    <div class="brand"><span class="brand-dot"></span>PlumVesta</div>
    <div class="avatar" role="img" aria-label="User profile photo"></div>
    <div class="welcome">Welcome<b>kk.</b></div>
    <svg class="caret" width="12" height="8" viewBox="0 0 12 8"><path d="M1 1l5 5 5-5" fill="none" stroke="#fff" stroke-width="2"/></svg>
  </header>

  <aside class="sidebar">
    <div class="search">Search<span class="search-btn"></span></div>
    <ul class="nav">
      <li><svg class="ico" viewBox="0 0 14 14"><path d="M1 7l6-5 6 5v6H9V9H5v4H1z" fill="#fff"/></svg><span style="padding-left:7px">Home</span></li>
      <li><svg class="ico" viewBox="0 0 14 14"><path d="M7 1a4 4 0 014 4v4l2 2H1l2-2V5a4 4 0 014-4zM5 12h4a2 2 0 01-4 0z" fill="#fff"/></svg>All Alerts</li>
      <li><svg class="ico" viewBox="0 0 14 14"><circle cx="7" cy="7" r="5" fill="none" stroke="#fff" stroke-width="3" stroke-dasharray="2.2 1.4"/><circle cx="7" cy="7" r="2.5" fill="#fff"/></svg>Mange</li>
      <li><svg class="ico" viewBox="0 0 14 14"><rect x="1" y="2" width="12" height="10" fill="none" stroke="#fff"/><path d="M1 5h12" stroke="#fff"/></svg>Campaigns<svg class="end" width="10" height="10" viewBox="0 0 10 10"><path d="M5 0v10M0 5h10" stroke="#fff" stroke-width="2"/></svg></li>
      <li class="group"><svg class="ico" viewBox="0 0 14 14"><rect x="1" y="2" width="12" height="10" fill="none" stroke="#fff"/><path d="M1 5h12" stroke="#fff"/></svg><span style="padding-left:3px">My Custom Campaign</span><svg class="end" width="11" height="7" viewBox="0 0 11 7"><path d="M1 6l4.5-4.5L10 6" fill="none" stroke="#fff" stroke-width="2"/></svg></li>
      <li class="sub active"><svg class="ico" viewBox="0 0 14 14"><rect x="1" y="1" width="12" height="12" fill="none" stroke="#fff"/><circle cx="8" cy="8" r="3" fill="none" stroke="#fff"/></svg>Overview</li>
      <li class="sub"><svg class="ico" viewBox="0 0 14 14"><path d="M3 1h6l3 3v9H3z" fill="none" stroke="#fff"/></svg>Files &amp; HonyTokens</li>
      <li class="sub"><svg class="ico" viewBox="0 0 14 14"><circle cx="7" cy="3" r="2" fill="#fff"/><circle cx="3" cy="9" r="2" fill="#fff"/><circle cx="11" cy="9" r="2" fill="#fff"/><path d="M1 14h12" stroke="#fff"/></svg>Resource</li>
      <li class="sub"><svg class="ico" viewBox="0 0 14 14"><path d="M7 1a4 4 0 014 4v4l2 2H1l2-2V5a4 4 0 014-4zM5 12h4a2 2 0 01-4 0z" fill="#fff"/></svg>Alerts</li>
      <li class="sub"><svg class="ico" viewBox="0 0 14 14"><circle cx="7" cy="7" r="5" fill="none" stroke="#fff" stroke-width="3" stroke-dasharray="2.2 1.4"/><circle cx="7" cy="7" r="2.5" fill="#fff"/></svg>Settings</li>
      <li class="sub group"><svg class="ico" viewBox="0 0 14 14"><rect x="1" y="2" width="12" height="10" fill="none" stroke="#fff"/><path d="M1 5h12" stroke="#fff"/></svg>Default Campaign<svg class="end" width="11" height="7" viewBox="0 0 11 7"><path d="M1 1l4.5 4.5L10 1" fill="none" stroke="#fff" stroke-width="2"/></svg></li>
    </ul>
  </aside>

  <div class="panel" style="top:107px;height:49px"><div class="panel-head" style="border:none;color:var(--ink)"><b style="font-weight:600">Overview</b> / My Custom Campaign</div></div>
  <div class="panel" style="top:160px;height:109px">
    <div class="eyebrow" style="top:14px">OVERVIEW</div>
    <div class="abs" style="left:16px;top:45px;width:44px;height:44px;border-radius:50%;background:var(--side);display:flex;align-items:center;justify-content:center"><svg width="24" height="20" viewBox="0 0 24 20"><path d="M3 8h5l9-6v16l-9-6H3z" fill="#f0a33a"/><path d="M20 6l3-2M20 10h3M20 14l3 2" stroke="#f0a33a" stroke-width="1.6"/></svg></div>
    <div class="abs" style="left:69px;top:44px;font-size:15px;font-weight:600">My Custom Campaign</div>
    <div class="small" style="left:69px;top:69px;font-size:11px">This Is My Custom Campagin For Finding</div>
    <div class="btn-new" style="left:1031px;top:40px;width:125px;height:40px">New Campaign <svg width="10" height="10" viewBox="0 0 10 10"><path d="M5 0v10M0 5h10" stroke="#f0a33a" stroke-width="2.4"/></svg></div>
  </div>

  <div class="panel" style="top:285px;height:297px">
    <div class="panel-head">Campaign Organisation</div>
    <div class="card card--beige" style="left:15px;top:68px;height:189px">
      <div class="icon-disc" style="left:29px;top:27px"><svg width="36" height="38" viewBox="0 0 36 38"><rect x="5" y="4" width="26" height="32" fill="none" stroke="#fff" stroke-width="2.4"/><path d="M11 10h4M21 10h4M11 17h4M21 17h4M11 24h4M21 24h4M15 36v-6h6v6" stroke="#fff" stroke-width="2.4"/></svg></div>
      <div class="abs" style="left:112px;top:20px;font-size:17px;font-weight:600;line-height:24px">Self - enabling Deliverables Proprietary<br>Limited</div>
      <div class="small" style="left:112px;top:72px">Standard 86</div>
      <div class="badge badge--orange" style="left:106px;top:102px"><svg width="26" height="24" viewBox="0 0 26 24"><circle cx="13" cy="4" r="3" fill="none" stroke="#243150" stroke-width="1.5"/><circle cx="5" cy="15" r="3" fill="none" stroke="#243150" stroke-width="1.5"/><circle cx="21" cy="15" r="3" fill="none" stroke="#243150" stroke-width="1.5"/><path d="M13 7v5M13 12L5 12M13 12h8M1 23a4 4 0 018 0M17 23a4 4 0 018 0M9 23a4 4 0 018 0" fill="none" stroke="#243150" stroke-width="1.5"/></svg></div>
      <div class="big-num" style="left:155px;top:100px">86</div>
    </div>
    <div class="card card--grey" style="left:582px;top:68px;height:189px">
      <div class="icon-disc" style="left:29px;top:27px"><svg width="36" height="38" viewBox="0 0 36 38"><rect x="5" y="4" width="26" height="32" fill="none" stroke="#fff" stroke-width="2.4"/><path d="M11 10h4M21 10h4M11 17h4M21 17h4M11 24h4M21 24h4M15 36v-6h6v6" stroke="#fff" stroke-width="2.4"/></svg></div>
      <div class="abs" style="left:112px;top:40px;font-size:17px;font-weight:600">Unleash bleeding - edge Mindshare</div>
      <div class="small" style="left:112px;top:66px">8 Hour Ago</div>
      <div class="badge badge--orange" style="left:106px;top:102px"><svg width="26" height="24" viewBox="0 0 26 24"><circle cx="13" cy="4" r="3" fill="none" stroke="#243150" stroke-width="1.5"/><circle cx="5" cy="15" r="3" fill="none" stroke="#243150" stroke-width="1.5"/><circle cx="21" cy="15" r="3" fill="none" stroke="#243150" stroke-width="1.5"/><path d="M13 7v5M13 12L5 12M13 12h8M1 23a4 4 0 018 0M17 23a4 4 0 018 0M9 23a4 4 0 018 0" fill="none" stroke="#243150" stroke-width="1.5"/></svg></div>
      <div class="big-num" style="left:155px;top:100px">8</div>
    </div>
  </div>

  <div class="panel" style="top:599px;height:317px">
    <div class="panel-head">Files &amp; HoneyTokens<span class="right-label" style="left:581px">Resources</span></div>
    <div class="card card--grey" style="left:15px;top:72px;height:188px">
      <div class="icon-disc" style="left:29px;top:26px"><svg width="40" height="38" viewBox="0 0 40 38"><path d="M4 14l9-8 8 6 12-9" fill="none" stroke="#fff" stroke-width="2"/><rect x="4" y="22" width="5" height="14" fill="none" stroke="#fff" stroke-width="2"/><rect x="13" y="18" width="5" height="18" fill="none" stroke="#fff" stroke-width="2"/><rect x="22" y="24" width="5" height="12" fill="none" stroke="#fff" stroke-width="2"/><rect x="31" y="15" width="5" height="21" fill="none" stroke="#fff" stroke-width="2"/></svg></div>
      <div class="abs" style="left:112px;top:44px;font-size:17px;font-weight:600">Statistics</div>
      <div class="badge badge--orange" style="left:106px;top:103px"><svg width="18" height="14" viewBox="0 0 18 14"><path d="M2 7l5 5 9-10" fill="none" stroke="#243150" stroke-width="3"/></svg></div>
      <div class="big-num" style="left:160px;top:100px">0</div>
      <div class="badge badge--navy" style="left:204px;top:103px"><svg width="16" height="20" viewBox="0 0 16 20"><path d="M1 1h9l5 5v13H1z" fill="#f0a33a"/><path d="M4 9h8M4 12h8M4 15h8" stroke="#243150" stroke-width="1.2"/></svg></div>
      <div class="big-num" style="left:258px;top:100px">30</div>
    </div>
    <div class="card card--beige" style="left:583px;top:72px;height:188px">
      <div class="icon-disc" style="left:30px;top:26px"><svg width="36" height="40" viewBox="0 0 36 40"><path d="M5 6h20l6 6v26H5z" fill="none" stroke="#fff" stroke-width="2.2"/><circle cx="18" cy="19" r="4" fill="none" stroke="#fff" stroke-width="2"/><path d="M11 30a7 7 0 0114 0M10 34h16" fill="none" stroke="#fff" stroke-width="2"/></svg></div>
      <div class="abs" style="left:113px;top:36px;font-size:17px;font-weight:600;line-height:24px">Generate A Collection Of Fictional Organistions,<br>Custom Templates , Uploaded Files And Logos.</div>
    </div>
  </div>

  <div class="panel" style="top:933px;height:189px">
    <div class="panel-head">Alerts</div>
    <div class="icon-disc" style="left:23px;top:78px"><svg width="38" height="34" viewBox="0 0 38 34"><rect x="2" y="4" width="26" height="20" fill="none" stroke="#f0a33a" stroke-width="2"/><path d="M2 4l13 11 13-11" fill="none" stroke="#f0a33a" stroke-width="2"/><path d="M27 14a6 6 0 016 6v5l2 3H19l2-3v-5a6 6 0 016-6zM24 30h6" fill="#243150" stroke="#f0a33a" stroke-width="2"/></svg></div>
    <div class="abs" style="left:106px;top:98px;font-size:17px;font-weight:600">Alert Statistics Will Apper Here</div>
  </div>
</section>

</div>
</body>
</html>
```